Marwick Family Chiropractic Stationary

The letterhead and business card must have our logo.
We would like to see the logo used in different ways ( It can be expanded upon in the stationary.)
Please use the the same or similar colors.
Must be eye catching and memorable.
Must be easy to read

Reason: The doctor has been too busy to make any final decisions. He would like to give himself a little more time.

Target Market(s)

Chiropractic Healthcare

Industry/Entity Type

Business

Requirements
Must have
• Dr. Leonard Marwick D.C.
Chiropractor

860-555-0183

417 Birchfield Road, 2nd Floor
Alderbrook 06091

drmarwick@marwickspine.example
www.marwickspine.example
www.facebook.com/MarwickFamilySpine
Should not have
• should not be difficult to read

```html
<!DOCTYPE html>
<html lang="en">
<head>
<meta charset="utf-8">
<title>Marwick Family Chiropractic – Business Cards</title>
<link href="https://fonts.googleapis.com/css2?family=Montserrat:wght@600;700&family=Questrial&display=swap" rel="stylesheet">
<style>
  :root {
    --backdrop: #e9e6e1;
    --card-black: #050505;
    --lime: #a4cd5a;
    --lime-soft: #8fbf45;
    --taupe: #8f877d;
    --light-text: #f2f2f2;
    --rule: #6b6b6b;
  }
  * { margin: 0; padding: 0; box-sizing: border-box; }
  html, body { width: 1200px; height: 724px; overflow: hidden; }
  body {
    background: var(--backdrop);
    position: relative;
    font-family: "Questrial", sans-serif;
    color: var(--light-text);
  }
  .card {
    position: absolute;
    width: 543px;
    height: 311px;
    overflow: hidden;
  }
  .card--front { left: 41px; top: 39px; background: var(--card-black); }
  .card--mark-dark { left: 615px; top: 38px; background: var(--card-black); }
  .card--wordmark { left: 41px; top: 374px; background: var(--card-black); }
  .card--mark-lime { left: 617px; top: 371px; background: var(--lime); }

  /* front card */
  .brand-lockup {
    position: absolute;
    left: 50px; top: 50px;
    width: 190px;
    text-align: center;
  }
  .brand-dot {
    width: 100px; height: 100px;
    border-radius: 50%;
    background: var(--lime-soft);
    margin: 0 auto 8px;
  }
  .brand-name {
    font-family: "Montserrat", sans-serif;
    font-weight: 700;
    color: var(--lime);
    font-size: 27px;
    letter-spacing: 1px;
    line-height: 1.05;
  }
  .brand-tagline {
    font-family: "Montserrat", sans-serif;
    font-weight: 600;
    color: var(--taupe);
    font-size: 11.5px;
    letter-spacing: 0.3px;
    margin-top: 2px;
  }
  .divider {
    position: absolute;
    left: 249px; top: 55px;
    width: 2px; height: 115px;
    background: linear-gradient(to bottom, transparent, #cfcfcf 40%, transparent);
  }
  .doctor {
    position: absolute;
    left: 275px; top: 56px;
  }
  .doctor-name { color: var(--lime); font-size: 16px; font-weight: 700; font-family: "Questrial", sans-serif; }
  .doctor-title { color: var(--taupe); font-size: 15px; margin-top: 1px; }
  .contact-list {
    position: absolute;
    left: 275px; top: 120px;
    list-style: none;
    font-size: 14px;
    line-height: 21.5px;
  }
  .contact-list li { display: flex; align-items: center; gap: 6px; }
  .contact-list svg { width: 10px; height: 10px; flex: none; }
  .base-rule {
    position: absolute;
    left: 0; right: 0; top: 266px;
    height: 3px;
    background: var(--rule);
  }
  .address-band {
    position: absolute;
    left: 0; right: 0; bottom: 0;
    height: 30px;
    background: var(--lime);
    color: #111;
    font-size: 14px;
    text-align: center;
    line-height: 30px;
  }

  /* mark cards */
  .mark {
    position: absolute;
    left: 50%; top: 36px;
    transform: translateX(-50%);
    text-align: center;
    width: 320px;
  }
  .mark-dot {
    width: 170px; height: 170px;
    border-radius: 50%;
    margin: 0 auto 12px;
  }
  .card--mark-dark .mark-dot { background: var(--lime-soft); }
  .card--mark-lime .mark-dot { background: #ffffff; }
  .mark-name {
    font-family: "Montserrat", sans-serif;
    font-weight: 600;
    font-size: 13px;
    letter-spacing: 1px;
  }
  .card--mark-dark .mark-name { color: var(--lime); }
  .card--mark-lime .mark-name { color: #ffffff; }
  .web {
    position: absolute;
    left: 0; right: 0; bottom: 22px;
    text-align: center;
    font-size: 15px;
    letter-spacing: 2.5px;
    color: #ffffff;
  }

  /* wordmark card */
  .pattern-field {
    position: absolute; inset: 0;
    background: radial-gradient(circle at 50% 50%, #1a1f12 0%, #0b0d08 70%);
  }
  .wordmark {
    position: absolute;
    left: 0; right: 0; top: 88px;
    text-align: center;
    font-family: "Montserrat", sans-serif;
    font-weight: 700;
  }
  .wordmark-primary { color: var(--lime); font-size: 62px; letter-spacing: 3px; line-height: 1; }
  .wordmark-secondary { color: var(--taupe); font-size: 25px; letter-spacing: 1.5px; margin-top: 8px; }
</style>
</head>
<body>

  <section class="card card--front">
    <div class="brand-lockup">
      <div class="brand-dot"></div>
      <div class="brand-name">MARWICK</div>
      <div class="brand-tagline">FAMILY CHIROPRACTIC</div>
    </div>
    <div class="divider"></div>
    <div class="doctor">
      <p class="doctor-name">Dr. Leonard Marwick D.C.</p>
      <p class="doctor-title">Chiropractor</p>
    </div>
    <ul class="contact-list">
      <li>
        <svg viewBox="0 0 10 10" aria-hidden="true"><circle cx="5" cy="5" r="4.3" fill="none" stroke="#fff" stroke-width="1"/><path d="M3.3 2.8 L4.2 2.6 L4.6 3.9 L4 4.3 Q4.7 5.6 5.8 6 L6.2 5.4 L7.4 5.8 L7.2 6.8 Q4 7 3.3 2.8Z" fill="#fff"/></svg>
        555-555-0183
      </li>
      <li>
        <svg viewBox="0 0 10 10" aria-hidden="true"><rect x="1" y="2.5" width="8" height="5.5" fill="none" stroke="#fff" stroke-width="1"/><path d="M1 2.5 L5 5.8 L9 2.5" fill="none" stroke="#fff" stroke-width="1"/></svg>
        mymarwick@marwickspine.example
      </li>
      <li>
        <svg viewBox="0 0 10 10" aria-hidden="true"><circle cx="5" cy="5" r="4.2" fill="none" stroke="#fff" stroke-width="0.9"/><ellipse cx="5" cy="5" rx="1.8" ry="4.2" fill="none" stroke="#fff" stroke-width="0.8"/><path d="M0.8 5 H9.2" stroke="#fff" stroke-width="0.8"/></svg>
        www.marwickspine.example
      </li>
      <li>
        <svg viewBox="0 0 10 10" aria-hidden="true"><rect x="0.5" y="0.5" width="9" height="9" fill="#fff"/></svg>
        MarwickFamilySpine
      </li>
    </ul>
    <div class="base-rule"></div>
    <div class="address-band">417 Birchfield Road, 2nd Floor, Alderbrook 06091</div>
  </section>

  <section class="card card--mark-dark">
    <div class="mark">
      <div class="mark-dot"></div>
      <div class="mark-name">MARWICK FAMILY CHIROPRACTIC</div>
    </div>
    <p class="web">www.marwickspine.example</p>
  </section>

  <section class="card card--wordmark">
    <div class="pattern-field" role="img" aria-label="Repeating pattern of small practice emblems on a dark background"></div>
    <div class="wordmark">
      <div class="wordmark-primary">MARWICK</div>
      <div class="wordmark-secondary">FAMILY CHIROPRACTIC</div>
    </div>
    <p class="web">www.marwickspine.example</p>
  </section>

  <section class="card card--mark-lime">
    <div class="mark">
      <div class="mark-dot"></div>
      <div class="mark-name">MARWICK FAMILY CHIROPRACTIC</div>
    </div>
    <p class="web">www.marwickspine.example</p>
  </section>

</body>
</html>
```